Business Card Design needed for start up company Halvora

In need of a new business card designed for a start up company based in Sydney, Halvora is a new start up innovative Company, our mission it to make property accessible for everyday Australian and to become the leading Real Estate platform in Australia. We want it to be fresh and clean.

Industry/Entity Type

Financial

Contact Information for Business Card

Section for Name
Section for Title

HALVORA - The Strength of Pooling
Mobile:
Direct:

Font styles to use
Sans Serif

Colors
33a6d7
0692cd
0255a3
ffffff

Requirements
Must have
• Logo, all business card details

```html
<!DOCTYPE html>
<html lang="en">
<head>
<meta charset="utf-8">
<title>Halvora Business Card</title>
<link href="https://fonts.googleapis.com/css2?family=Montserrat:wght@400;600;800&display=swap" rel="stylesheet">
<style>
  :root {
    --sky: #33a6d7;
    --azure: #0692cd;
    --navy: #0255a3;
    --navy-deep: #1d3f86;
    --white: #ffffff;
    --paper: #f4f5f6;
    --ink: #3a3f47;
    --stage: #e9ecef;
  }
  * { margin: 0; padding: 0; box-sizing: border-box; }
  html, body { width: 1200px; height: 911px; overflow: hidden; }
  body {
    background: var(--stage);
    font-family: "Montserrat", Arial, sans-serif;
    position: relative;
  }
  .card {
    position: absolute;
    width: 540px;
    height: 309px;
    border-radius: 22px;
    overflow: hidden;
    box-shadow: 0 10px 28px rgba(0,0,0,0.18);
  }
  .card-front { left: 80px; top: 110px; background: var(--paper); }
  .card-back { left: 580px; top: 490px; background: var(--sky); }

  .front-band { position: absolute; inset: 0; width: 100%; height: 100%; }

  .holder { position: absolute; top: 26px; right: 34px; text-align: right; }
  .holder-name {
    color: var(--sky); font-weight: 800; font-size: 21px; letter-spacing: 0.5px;
  }
  .holder-title {
    color: var(--white); font-weight: 400; font-size: 13px; letter-spacing: 0.5px; margin-top: 2px;
  }

  .brand { position: absolute; display: flex; align-items: center; gap: 10px; }
  .brand-dot { border-radius: 50%; flex: none; }
  .brand-name { font-weight: 800; letter-spacing: -1px; line-height: 1; }

  .card-front .brand { left: 40px; bottom: 42px; }
  .card-front .brand-dot { width: 40px; height: 40px; background: var(--azure); }
  .card-front .brand-name { font-size: 44px; color: var(--navy-deep); }

  .contact {
    position: absolute; right: 30px; top: 128px;
    padding-left: 18px; border-left: 1px solid #c9ccd1;
    color: var(--ink); font-size: 11.5px; line-height: 1.55;
  }
  .contact-address { margin-bottom: 6px; }
  .contact-row { display: flex; align-items: center; gap: 7px; }
  .contact-row svg { width: 11px; height: 11px; fill: var(--navy-deep); flex: none; }

  .card-back .brand { left: 50%; top: 92px; transform: translateX(-50%); }
  .card-back .brand-dot { width: 52px; height: 52px; background: var(--white); }
  .card-back .brand-name { font-size: 64px; color: var(--white); }
  .tagline {
    position: absolute; left: 0; right: 0; top: 190px;
    text-align: center; color: var(--white); font-size: 14px; font-style: normal; letter-spacing: 0.6px;
  }
</style>
</head>
<body>

<section class="card card-front" aria-label="Business card front">
  <svg class="front-band" viewBox="0 0 540 309" preserveAspectRatio="none" aria-hidden="true">
    <path d="M0 0 H540 V70 C360 78 170 130 0 230 Z" fill="var(--navy-deep)"/>
    <path d="M0 230 C170 130 360 78 540 70 V80 C360 88 175 140 0 244 Z" fill="var(--sky)"/>
  </svg>
  <div class="holder">
    <div class="holder-name">LIAM CARTER</div>
    <div class="holder-title">CEO/FOUNDER</div>
  </div>
  <div class="brand">
    <span class="brand-dot"></span>
    <span class="brand-name">HALVORA</span>
  </div>
  <div class="contact">
    <div class="contact-address">42 Wattle Grove<br>Sydney, NSW 2000</div>
    <div class="contact-row">
      <svg viewBox="0 0 12 12"><path d="M2.5 1 4.5 1 5.3 3.6 4 4.6C4.7 6 6 7.3 7.4 8L8.4 6.7 11 7.5 11 9.5C11 10.3 10.3 11 9.5 11 5 11 1 7 1 2.5 1 1.7 1.7 1 2.5 1Z"/></svg>
      <span>0412 558 903</span>
    </div>
    <div class="contact-row">
      <svg viewBox="0 0 12 12"><path d="M1 2H11V10H1Z M2 3V9H10V3Z" fill-rule="evenodd"/></svg>
      <span>02 9184 6627</span>
    </div>
    <div class="contact-row">
      <svg viewBox="0 0 12 12"><path d="M1 2.5H11V9.5H1Z M1 2.5 6 6.5 11 2.5" fill="none" stroke="var(--navy-deep)" stroke-width="1.2"/></svg>
      <span>liam@halvora.com</span>
    </div>
    <div class="contact-row">
      <svg viewBox="0 0 12 12"><circle cx="6" cy="6" r="5"/></svg>
      <span>www.halvora.com</span>
    </div>
  </div>
</section>

<section class="card card-back" aria-label="Business card back">
  <div class="brand">
    <span class="brand-dot"></span>
    <span class="brand-name">HALVORA</span>
  </div>
  <p class="tagline">The Strength of Pooling</p>
</section>

</body>
</html>
```